VL Business Card

Used Car Sales
We are trying to recreate the image of our license plate on business cards,
it is a red background with a white oval that is open on the ends
I attempted to upload the image but it was a dismal failure when the products arrived
the lettering was too small and the edges were white
I think maybe the red needs some texture in it, still red but something that doesn't look so flat
and maybe a beveled edge around the white (not sure)

Target Market(s)

Adults 25-65 that drive

Industry/Entity Type

Business

Contact Information for Business Card

Danielle Hargrove, Sales Manager, FAIRVIEW AUTO SALES, INC., 462 Birch Lane, Harlow, OH 45899,
555 555-0172 (office), 555 555-0186 (fax) - We Finance everyone with approved credit
FairviewAutoSales.Example

On Back: Financing Available - We Finance everyone with approved credit
Easy Payments: Monthly, Semi-Monthly or Weekly
Ask about our Layaway plan
Open Mon-Sat
8:30 AM - 5 PM

Requirements
Must have
• We want to match the license plate (minus holes for screws)

```html
<!DOCTYPE html>
<html lang="en">
<head>
<meta charset="utf-8">
<title>VL Business Card</title>
<link rel="stylesheet" href="https://fonts.googleapis.com/css2?family=Libre+Franklin:wght@400;500;600;700;800;900&display=swap">
<style>
  :root {
    --stage: #111111;
    --plate-red: #b5272f;
    --plate-red-dark: #a01f27;
    --ink: #151515;
    --brand-red: #d7373a;
    --metal-light: #f4f4f6;
    --metal-mid: #d9d9dd;
    --metal-dark: #c3c3c8;
    --rim: #9d9da3;
    --screw: #3a3a3a;
  }
  * { box-sizing: border-box; margin: 0; padding: 0; }
  html, body { width: 1200px; height: 1000px; overflow: hidden; background: var(--stage); }
  body { position: relative; font-family: "Libre Franklin", Arial, sans-serif; color: var(--ink); }

  .card {
    position: absolute; left: 259px; width: 683px; height: 389px;
    background:
      repeating-linear-gradient(45deg, rgba(0,0,0,.03) 0 2px, rgba(255,255,255,.02) 2px 4px),
      linear-gradient(180deg, var(--plate-red), var(--plate-red-dark));
  }
  .card--front { top: 76px; }
  .card--back { top: 528px; }

  .plate {
    position: absolute; left: 2px; right: 2px; top: 27px; height: 337px;
    border-radius: 20px;
    background: linear-gradient(180deg, var(--metal-dark) 0%, var(--metal-mid) 20%, var(--metal-light) 50%, var(--metal-mid) 80%, var(--metal-dark) 100%);
    box-shadow: inset 0 0 0 2px #e9e9ec, 0 1px 2px rgba(0,0,0,.35);
  }
  .plate::before {
    content: ""; position: absolute; inset: 5px; border-radius: 16px;
    border: 2px solid var(--rim);
    box-shadow: inset 0 0 0 1px rgba(255,255,255,.7), 0 0 0 1px rgba(255,255,255,.6);
  }

  .screw {
    position: absolute; width: 17px; height: 17px; border-radius: 50%;
    background: radial-gradient(circle at 40% 35%, #8a8a8a, var(--screw) 65%, #1e1e1e);
    box-shadow: 0 1px 1px rgba(255,255,255,.6);
  }
  .screw::after {
    content: ""; position: absolute; left: 2px; right: 2px; top: 7px; height: 3px;
    background: #161616; transform: rotate(-40deg);
  }
  .screw--tl { left: 23px; top: 15px; }
  .screw--tr { right: 23px; top: 15px; }
  .screw--bl { left: 23px; bottom: 18px; }
  .screw--br { right: 23px; bottom: 18px; }

  .line { position: absolute; left: 0; right: 0; text-align: center; white-space: nowrap; }

  .name { top: 45px; font-size: 39px; font-weight: 500; letter-spacing: .3px; }
  .title { top: 89px; font-size: 24px; font-weight: 400; letter-spacing: .5px; }
  .title span { position: relative; display: inline-block; padding: 0 8px; }
  .title span::before, .title span::after {
    content: ""; position: absolute; top: 50%; width: 46px; height: 1px; background: var(--ink);
  }
  .title span::before { right: 100%; }
  .title span::after { left: 100%; }
  .company { top: 149px; font-size: 37px; font-weight: 900; color: var(--brand-red); letter-spacing: .3px; text-shadow: 0 1px 0 rgba(0,0,0,.15); }
  .address { top: 225px; font-size: 27px; font-weight: 400; letter-spacing: .4px; }
  .phones { top: 260px; font-size: 22px; }
  .phones small { font-size: 18px; }
  .phones .gap { display: inline-block; width: 14px; }

  .finance-head { top: 27px; font-size: 25px; font-weight: 600; }
  .finance-sub { top: 62px; font-size: 21px; font-weight: 600; }
  .web { top: 105px; font-size: 25px; font-weight: 900; color: var(--brand-red); letter-spacing: 0; }
  .detail { font-size: 22px; }
  .detail--1 { top: 153px; }
  .detail--2 { top: 183px; }
  .detail--3 { top: 215px; font-size: 19px; letter-spacing: -.2px; }
  .detail--4 { top: 242px; }
  .hours { top: 286px; font-size: 23px; font-weight: 600; word-spacing: 0; }
</style>
</head>
<body>
  <section class="card card--front" aria-label="Business card front">
    <div class="plate">
      <span class="screw screw--tl"></span><span class="screw screw--tr"></span>
      <span class="screw screw--bl"></span><span class="screw screw--br"></span>
      <p class="line name">Danielle Hargrove</p>
      <p class="line title"><span>SALES MANAGER</span></p>
      <p class="line company">FAIRVIEW AUTO SALES, INC.</p>
      <p class="line address">462 Birch Lane, Harlow, OH 45899</p>
      <p class="line phones">555 555 0172 <small>(office)</small><span class="gap"></span>555 555 0186 <small>(fax)</small></p>
    </div>
  </section>

  <section class="card card--back" aria-label="Business card back">
    <div class="plate">
      <span class="screw screw--tl"></span><span class="screw screw--tr"></span>
      <span class="screw screw--bl"></span><span class="screw screw--br"></span>
      <p class="line finance-head">WE FINANCE</p>
      <p class="line finance-sub">EVERYONE WITH APPROVED CREDIT!</p>
      <p class="line web">FAIRVIEWAUTOSALES.EXAMPLE</p>
      <p class="line detail detail--1">On Back: Financing Available</p>
      <p class="line detail detail--2">We Finance everyone with approved credit</p>
      <p class="line detail detail--3">Easy Payments: Monthly, Semi-Monthly or Weekly</p>
      <p class="line detail detail--4">Ask about our Layaway plan.</p>
      <p class="line hours">OPEN&nbsp; MON - SAT&nbsp;&nbsp; 8:30 AM - 5 PM</p>
    </div>
  </section>
</body>
</html>
```